The Velvet Rig

need a business card for a dj and sound equipment hire(rentals) business based in Melbourne. i have attached a current card get an idea. card needs to be unique professional looking.

ps.this card is not for a DJ. it's a rental business of dj equipment and pa systems.

Industry/Entity Type

Business

Font styles to use
Sans Serif
Script

Requirements
Must have
• Business Name: THE VELVET RIG
Contact Person: KIERAN MALLORY
Mobile: 047 VELVET 91
Email: KIERAN@THEVELVETRIG.COM.AU
Website: WWW.THEVELVETRIG.COM.AU
Pixelwall: WWW.PIXELWALL.CM/THEVELVETRIG.COM.AU

```html
<!DOCTYPE html>
<html lang="en">
<head>
<meta charset="utf-8">
<title>The Velvet Rig – Business Card</title>
<link rel="stylesheet" href="https://fonts.googleapis.com/css2?family=Audiowide&family=Arimo:wght@400&display=swap">
<style>
  :root {
    --page-bg: #e6e4e1;
    --ink-dark: #161616;
    --band-black: #141414;
    --silver-light: #d4d4d4;
    --silver-mid: #a3a3a3;
    --silver-dark: #6e6e6e;
    --ring-grey: #8a8a8a;
    --text-light: #f2f2f2;
    --text-soft: #dcdcdc;
    --accent-red: #d8262a;
  }
  html, body {
    margin: 0;
    width: 1200px;
    height: 1000px;
    overflow: hidden;
    background: var(--page-bg);
  }
  .canvas {
    position: relative;
    width: 1200px;
    height: 1000px;
  }
  .card {
    position: absolute;
    left: 100px;
    top: 214px;
    width: 1000px;
    height: 572px;
    overflow: hidden;
    border-radius: 4px;
    box-shadow: 0 10px 30px rgba(0,0,0,0.25);
    background: var(--band-black);
  }
  .band { position: absolute; left: 0; width: 100%; }
  .band-top {
    top: 0; height: 160px;
    background: linear-gradient(180deg, var(--silver-dark) 0%, var(--silver-mid) 45%, var(--silver-light) 100%);
  }
  .band-dark {
    top: 160px; height: 175px;
    background: linear-gradient(180deg, #0e0e0e 0%, #262626 100%);
  }
  .band-silver {
    top: 335px; height: 105px;
    background: linear-gradient(90deg, #2a2a2a 0%, #b9b9b9 30%, #9c9c9c 65%, #d0d0d0 100%);
  }
  .band-bottom {
    top: 440px; height: 132px;
    background: linear-gradient(90deg, #0c0c0c 0%, #3a3a3a 55%, #1a1a1a 100%);
  }
  .business-name {
    position: absolute;
    left: 70px;
    top: 42px;
    margin: 0;
    font-family: "Audiowide", sans-serif;
    font-weight: 400;
    font-size: 60px;
    letter-spacing: 4px;
    color: var(--ink-dark);
  }
  .photo-badge {
    position: absolute;
    left: 95px;
    top: 105px;
    width: 310px;
    height: 310px;
  }
  .contact {
    position: absolute;
    left: 470px;
    top: 222px;
  }
  .contact-name {
    margin: 0;
    font-family: "Audiowide", sans-serif;
    font-size: 40px;
    letter-spacing: 3px;
    color: transparent;
    -webkit-text-stroke: 1.5px var(--text-light);
  }
  .contact-phone {
    margin: 6px 0 0;
    font-family: "Arimo", sans-serif;
    font-size: 28px;
    letter-spacing: 1px;
    color: var(--text-soft);
  }
  .contact-lines {
    margin: 34px 0 0;
    padding: 0;
    list-style: none;
    font-family: "Arimo", sans-serif;
    font-size: 27px;
    line-height: 36px;
    color: var(--text-light);
  }
</style>
</head>
<body>
<main class="canvas">
  <section class="card" aria-label="The Velvet Rig business card">
    <div class="band band-top"></div>
    <div class="band band-dark"></div>
    <div class="band band-silver"></div>
    <div class="band band-bottom"></div>

    <h1 class="business-name">THE VELVET RIG</h1>

    <svg class="photo-badge" viewBox="0 0 310 310">
      <defs>
        <radialGradient id="mixerTones" cx="50%" cy="55%" r="60%">
          <stop offset="0%" stop-color="#5a5a5a"/>
          <stop offset="60%" stop-color="#2b2b2b"/>
          <stop offset="100%" stop-color="#111"/>
        </radialGradient>
        <linearGradient id="redGlow" x1="0" y1="0" x2="0" y2="1">
          <stop offset="0%" stop-color="#d8262a" stop-opacity="0"/>
          <stop offset="25%" stop-color="#d8262a" stop-opacity="0.55"/>
          <stop offset="45%" stop-color="#d8262a" stop-opacity="0"/>
        </linearGradient>
      </defs>
      <circle cx="155" cy="155" r="152" fill="var(--ring-grey)"/>
      <g role="img" aria-label="Photo of a sound mixing desk with a grid of hire equipment thumbnails">
        <circle cx="155" cy="155" r="130" fill="url(#mixerTones)"/>
        <circle cx="155" cy="155" r="130" fill="url(#redGlow)"/>
      </g>
    </svg>

    <div class="contact">
      <p class="contact-name">KIERAN MALLORY</p>
      <p class="contact-phone">0491570118</p>
      <ul class="contact-lines">
        <li>kieran@thevelvetrig.com.au</li>
        <li>www.thevelvetrig.com.au</li>
        <li>pixelwall.cm/thevelvetrig.com.au</li>
      </ul>
    </div>
  </section>
</main>
</body>
</html>
```